Existing Website Requiring new Pages

I have an existing word press website that was built using elementor.
Website: www.tallowcrestcare.com.au
I require the Vacancies page (https://www.tallowcrestcare.com.au/vacancies/) to be modified to display our new properties along with minor tweaks to how the information is presented.
The vacancies to be displayed are the exactly the same as those that are located on the homepage of QMR website (https://qmr.org.au/)
The new pages that link off the Vacancies tab will require custom design.
There are roughly 8 pages/properties to be incorporated. i wish for the design to be very similar to that displayed in the following link; https://www.polunda.com.au/vacancies/merrylands
Along with this the back end has not been updated for the last 3 years so it also requires some maintenance.
Website is in the disability industry and the custom pages will display information relative to Property Vacancies.
I have attached a ZIP file with some design guides, the information for each of the properties (which will need to be modified to show our business name Tallowcrest Care) and the example of how it is to look based off the Polunda website.
If you guys have any suggestions or ideas on how to make this more presentable or possible i'm open to your ideas.
Target Market(s)
People looking for SDA properties custom built for people with a disability
Industry/Entity Type
Disability
Coding
Coded - Design and coding required
Number of Pages Required
5+ page

```html
<!DOCTYPE html>
<html lang="en">
<head>
<meta charset="utf-8">
<title>Vacancies – Tallowcrest Care</title>
<link rel="stylesheet" href="https://fonts.googleapis.com/css2?family=Montserrat:wght@400;500;600;700&family=Roboto:wght@400;500&display=swap">
<style>
:root{
  --yellow:#fbb92f;
  --purple:#7b5fcf;
  --red:#e8384f;
  --ink:#1c1c1c;
  --muted:#8a8a8a;
  --line:#e6e6e6;
  --nav-active:#f08a5d;
  --brand:#d9488f;
  --footer-bar:#2a2a2a;
}
*{box-sizing:border-box;margin:0;padding:0}
html,body{width:1200px;height:4054px;overflow:hidden}
body{position:relative;background:#fff;font-family:"Montserrat",sans-serif;color:var(--ink)}

/* header */
.site-header{position:absolute;left:0;top:0;width:1200px;height:154px}
.brand{position:absolute;display:flex;align-items:center;gap:8px;color:var(--brand);font-family:"Montserrat",sans-serif;font-weight:600}
.brand-dot{width:14px;height:14px;border-radius:50%;background:var(--brand)}
.site-header .brand{left:108px;top:64px;font-size:19px}
.main-nav{position:absolute;top:75px;left:557px;display:flex;gap:23px;font-size:10px;font-weight:600;letter-spacing:.8px}
.main-nav a{color:#333;text-decoration:none}
.main-nav a.is-current{color:var(--nav-active)}

/* hero */
.hero-photo{position:absolute;left:0;top:154px;width:701px;height:515px;background:linear-gradient(160deg,#c9d0bf 0%,#8ea56b 40%,#5b7a3a 75%,#3f5a2b 100%)}
.hero-panel{position:absolute;left:701px;top:154px;width:499px;height:430px;background:var(--yellow);color:#fff}
.hero-panel h1{position:absolute;left:42px;top:130px;font-family:"Roboto",sans-serif;font-weight:500;font-size:58px;line-height:1}
.hero-panel p{position:absolute;left:42px;top:202px;font-family:"Roboto",sans-serif;font-size:32px;line-height:43px;width:330px}
.hero-panel svg{position:absolute;left:42px;top:316px}
.search-bar{position:absolute;left:620px;top:584px;width:580px;height:85px;background:#fff;border-radius:6px 0 0 0}
.search-field{position:absolute;top:32px;width:143px}
.search-field label{display:block;font-size:8px;font-weight:600;color:#333;margin-bottom:7px}
.search-field .select{height:31px;border:1px solid #d6d6d6;border-radius:3px;font-size:10px;color:#333;padding:0 12px;display:flex;align-items:center;justify-content:space-between}
.search-btn{position:absolute;left:470px;top:49px;width:97px;height:31px;background:var(--purple);color:#fff;font-size:12px;font-weight:600;border-radius:3px;display:flex;align-items:center;justify-content:center}

/* intro */
.intro{position:absolute;left:158px;top:775px;width:380px}
.intro h2{font-family:"Roboto",sans-serif;font-weight:500;font-size:38px;line-height:43px;color:#111}
.intro .rule{margin-top:33px;width:306px;height:1px;background:#555}
.intro svg{margin-top:20px}

/* cards */
.listing{position:absolute;width:359px;height:397px}
.listing .photo{position:absolute;inset:0}
.listing .tags{position:absolute;top:16px;left:16px;right:16px;display:flex;gap:4px}
.tag{font-size:7px;font-weight:700;color:#fff;padding:3px 6px;border-radius:2px;text-transform:uppercase;letter-spacing:.2px}
.tag.feat{background:var(--purple);margin-right:auto}
.tag.hot{background:var(--red)}
.tags .spacer{margin-right:auto}
.listing .info{position:absolute;left:0;bottom:0;width:254px;height:104px;background:#fff;padding-top:22px}
.info h3{font-size:11.5px;font-weight:600;white-space:nowrap;overflow:hidden;color:#111}
.info .suburb{font-size:9.5px;color:var(--muted);margin-top:3px}
.info .features{font-size:9px;color:#222;margin-top:9px;line-height:16px;text-transform:uppercase;width:240px}
.details-btn{position:absolute;left:-3px;top:381px;width:72px;height:28px;background:var(--yellow);color:#fff;font-size:10.5px;font-weight:600;border-radius:3px;display:flex;align-items:center;justify-content:center}

.sky-brick{background:linear-gradient(180deg,#8db5e0 0%,#b9cfe8 30%,#8a7565 55%,#5a4f47 80%,#8f8f8a 100%)}
.grey-house{background:linear-gradient(180deg,#e9eaeb 0%,#bdbdbd 35%,#7d7068 65%,#6e6a66 100%)}
.cloud-villa{background:linear-gradient(180deg,#4f86cf 0%,#c8d6e6 35%,#3f4955 60%,#7f8c6e 100%)}
.kitchen{background:linear-gradient(180deg,#f1f1f1 0%,#e2e2e2 45%,#7fb08b 60%,#dcdcdc 100%)}
.red-brick{background:linear-gradient(180deg,#d9dde3 0%,#a66b50 30%,#8c5a43 70%,#9a9a99 100%)}
.dark-villa{background:linear-gradient(180deg,#cdd3d8 0%,#b9bfc4 40%,#565a5e 65%,#8d8d8d 100%)}

/* map */
.map-title{position:absolute;left:111px;top:3242px;font-family:"Roboto",sans-serif;font-weight:400;font-size:30px;color:#111}
.map{position:absolute;left:110px;top:3305px;width:950px;height:395px;border-radius:4px;background:linear-gradient(90deg,#b9d7a4 0%,#d5e4cc 35%,#e9ece6 60%,#dfe7ec 80%,#b8d3ea 100%)}
.to-top{position:absolute;left:1143px;top:3502px;width:30px;height:30px;background:#9a9a9a;border-radius:2px}

/* footer */
.site-footer{position:absolute;left:0;top:3722px;width:1200px;height:272px;box-shadow:0 -6px 12px rgba(0,0,0,.05)}
.site-footer .brand{left:143px;top:90px;font-size:19px}
.contact{position:absolute;left:140px;top:192px;font-size:11px;color:var(--muted);line-height:20px}
.contact li{list-style:none;display:flex;align-items:center;gap:7px}
.socials{position:absolute;left:522px;top:60px;display:flex;flex-direction:column;gap:11px}
.socials span{width:26px;height:26px;border-radius:50%;background:#1a2b4a}
.socials span:first-child{background:#6b3fa0}
.foot-col{position:absolute;top:50px;width:210px}
.foot-col h4{font-size:11.5px;font-weight:500;letter-spacing:.6px;color:#1a2b4a;border-left:3px solid #3b7bd4;padding-left:10px;padding-bottom:10px;border-bottom:1px solid var(--line)}
.foot-col li{list-style:none;font-size:10.5px;color:var(--muted);padding:10px 0 7px;border-bottom:1px solid var(--line);line-height:17px}
.copyright{position:absolute;left:0;top:3994px;width:1200px;height:60px;background:var(--footer-bar);color:#bbb;font-size:9px;display:flex;align-items:center;justify-content:center}
</style>
</head>
<body>

<header class="site-header">
  <div class="brand"><span class="brand-dot"></span>Tallowcrest Care</div>
  <nav class="main-nav">
    <a class="is-current" href="#">HOME</a>
    <a href="#">ABOUT US</a>
    <a href="#">WHAT WE DO ▾</a>
    <a href="#">REFERRALS</a>
    <a href="#">FEEDBACK</a>
    <a href="#">CONTACT US</a>
  </nav>
</header>

<div class="hero-photo" role="img" aria-label="Woman in a wheelchair working on a laptop in a sunny garden"></div>
<section class="hero-panel">
  <h1>Vacancies</h1>
  <p>We can help you find your next home</p>
  <svg width="50" height="12" viewBox="0 0 50 12"><path d="M0 6h48M42 1l6 5-6 5" fill="none" stroke="#fff" stroke-width="1.5"/></svg>
</section>
<form class="search-bar">
  <div class="search-field" style="left:20px"><label>CURRENT OR FUTURE</label><div class="select">Both<span>⇕</span></div></div>
  <div class="search-field" style="left:171px"><label>DESIGN CATEGORY</label><div class="select">All Categories<span>⇕</span></div></div>
  <div class="search-field" style="left:321px"><label>LOCATION</label><div class="select">All Suburbs<span>⇕</span></div></div>
  <div class="search-btn">Search</div>
</form>

<section class="intro">
  <h2>Tallowcrestcare is a resident centred SDA provider</h2>
  <div class="rule"></div>
  <svg width="50" height="12" viewBox="0 0 50 12"><path d="M0 6h48M42 1l6 5-6 5" fill="none" stroke="#f0a030" stroke-width="1.5"/></svg>
</section>

<!-- right column -->
<article class="listing" style="left:655px;top:769px">
  <div class="photo sky-brick" role="img" aria-label="Two-storey brick home in Greystanes"></div>
  <div class="tags"><span class="tag feat">Featured</span><span class="tag hot">Almost full - apply now!</span><span class="tag hot">Apply now</span></div>
  <div class="info"><h3>SDA in Greystanes</h3><p class="suburb">Greystanes</p><p class="features">Fully accessible, high physical support</p></div>
  <div class="details-btn">Details</div>
</article>
<article class="listing" style="left:655px;top:1252px">
  <div class="photo grey-house" role="img" aria-label="Townhouse with balcony in Werrington"></div>
  <div class="tags"><span class="tag feat">Featured</span><span class="tag hot">Available now</span><span class="tag hot">Current vacancy</span></div>
  <div class="info"><h3>SDA in Werrington</h3><p class="suburb">Werrington</p><p class="features">Fully accessible, improved liveability</p></div>
  <div class="details-btn">Details</div>
</article>
<article class="listing" style="left:655px;top:1753px">
  <div class="photo sky-brick" role="img" aria-label="Modern brick duplex in West Pennant Hills"></div>
  <div class="tags"><span class="spacer"></span><span class="tag hot">Current vacancy</span><span class="tag hot">Apply now</span></div>
  <div class="info"><h3>SDA in West Pennant Hills</h3><p class="suburb">West Pennant Hills</p><p class="features">High physical support</p></div>
  <div class="details-btn">Details</div>
</article>
<article class="listing" style="left:655px;top:2237px">
  <div class="photo kitchen" role="img" aria-label="Kitchen with green tiled splashback"></div>
  <div class="tags"><span class="spacer"></span><span class="tag hot">Register your interest today</span><span class="tag hot">Apply now</span></div>
  <div class="info"><h3>SDA in Werrington</h3><p class="suburb">Austral</p><p class="features">Fully accessible, high physical support, robust</p></div>
  <div class="details-btn">Details</div>
</article>
<article class="listing" style="left:655px;top:2737px">
  <div class="photo dark-villa" role="img" aria-label="Single-storey dark brick villa in Blacktown"></div>
  <div class="tags"><span class="spacer"></span><span class="tag hot">Expression of interest</span><span class="tag hot">Apply now</span></div>
  <div class="info"><h3>SDA in Blacktown – 1 bedroom villas av</h3><p class="suburb">Blacktown</p><p class="features">High physical support</p></div>
  <div class="details-btn">Details</div>
</article>

<!-- left column -->
<article class="listing" style="left:173px;top:1011px">
  <div class="photo grey-house" role="img" aria-label="Two-storey home with garage in Jordan Springs"></div>
  <div class="tags"><span class="tag feat">Featured</span><span class="tag hot">Available now</span><span class="tag hot">Current vacancy</span></div>
  <div class="info"><h3>SDA in Jordan Springs</h3><p class="suburb">Jordan Springs</p><p class="features">Fully accessible, improved liveability</p></div>
  <div class="details-btn">Details</div>
</article>
<article class="listing" style="left:173px;top:1509px">
  <div class="photo cloud-villa" role="img" aria-label="New villas under a cloudy sky in Wentworthville"></div>
  <div class="tags"><span class="tag feat">Featured</span><span class="tag hot">Available now</span><span class="tag hot">New construction</span></div>
  <div class="info"><h3>SDA villas in Wentworthville</h3><p class="suburb">Wentworthville</p><p class="features">Fully accessible, high physical support, improved liveability</p></div>
  <div class="details-btn">Details</div>
</article>
<article class="listing" style="left:173px;top:1996px">
  <div class="photo sky-brick" role="img" aria-label="Newly built brick home in Guildford West"></div>
  <div class="tags"><span class="spacer"></span><span class="tag hot">New construction</span><span class="tag hot">Apply now</span></div>
  <div class="info"><h3>SDA in Guildford West</h3><p class="suburb">Guildford West</p><p class="features">Fully accessible, high physical support</p></div>
  <div class="details-btn">Details</div>
</article>
<article class="listing" style="left:173px;top:2493px">
  <div class="photo red-brick" role="img" aria-label="Red brick townhouses in Merrylands"></div>
  <div class="tags"><span class="spacer"></span><span class="tag hot">Available now</span><span class="tag hot">Current vacancy</span></div>
  <div class="info"><h3>SDA in Merrylands</h3><p class="suburb">Merrylands</p><p class="features">Fully accessible, high physical support</p></div>
  <div class="details-btn">Details</div>
</article>

<h2 class="map-title">View our SDA vacancies and homes being built</h2>
<div class="map" role="img" aria-label="Map of western Sydney showing SDA vacancy locations"></div>
<div class="to-top"></div>

<footer class="site-footer">
  <div class="brand"><span class="brand-dot"></span>Tallowcrest Care</div>
  <ul class="contact">
    <li><svg width="11" height="9" viewBox="0 0 11 9"><rect x=".5" y=".5" width="10" height="8" fill="none" stroke="#e8384f"/><path d="M.5 .5l5 4 5-4" fill="none" stroke="#e8384f"/></svg>Email: info@tallowcrestcare.com.au</li>
    <li><svg width="11" height="11" viewBox="0 0 11 11"><path d="M2 1l2 2-1 2 3 3 2-1 2 2-2 2C4 10 1 7 0 3z" fill="#e8384f"/></svg>Phone: +61 0412 555 308</li>
    <li><svg width="11" height="11" viewBox="0 0 11 11"><circle cx="5.5" cy="5.5" r="4.5" fill="none" stroke="#e8384f"/><path d="M5.5 3v3h2" fill="none" stroke="#e8384f"/></svg>Operating Hours: 9AM To 5PM Monday - Friday</li>
  </ul>
  <div class="socials"><span></span><span></span><span></span><span></span></div>
  <div class="foot-col" style="left:605px">
    <h4>ACCOMMODATION</h4>
    <ul><li>Supported Independent Living (SIL)</li><li>Specialist Disability Accommodation (SDA)</li><li>Short term Accommodation (Respite)</li><li>Vacancies</li></ul>
  </div>
  <div class="foot-col" style="left:838px">
    <h4>WHAT WE DO</h4>
    <ul><li>In Home Care</li><li>Social &amp; Community Services</li><li>Therapeutic Supports</li><li>Support Coordination</li><li>Home Modifications</li></ul>
  </div>
</footer>
<div class="copyright">© Copyright 2021 | Tallowcrest Care | All Rights Reserved.</div>

</body>
</html>
```